Design WordPress Website for Contractor App Website

I need a graphic design for a WordPress website for our SaaS called Velumar Software. Please design the landing (Home) page first, before designing other pages. You can design other pages if your landing page is selected.

The design should be modern with a startup feel. The link to the trelvano doc below provides more information. And the attached image has the logo and some screenshots you can use. Copy text from the competitor's site listed as placeholders text or use Lorem Ipsum where needed.

https://files.trelvanodocs.net/doc/7QpXrLm2ZkW9vTbN4cHsYd1FjA8gEo3UiR6nKwBq/view?mode=share

Target Market(s)

Contractors, painters, plumbers, handymen, electricians, carpenters, landscapers, roofers, home service business.

Industry/Entity Type

Home Improvement

Number of Pages Required

5+ page

Colors
ffc214
34a6d7
9bcb3c

Requirements
Must have
• Look, professionals
Pindle Shelf and Apdex Shelf download icons
Focused on contractors
Nice to have
• Section for video

```html
<!DOCTYPE html>
<html lang="en">
<head>
<meta charset="utf-8">
<title>Velumar Software – Field Service App for Contractors</title>
<link href="https://fonts.googleapis.com/css2?family=Poppins:wght@400;500;600&family=Nunito+Sans:wght@400;600;700&display=swap" rel="stylesheet">
<style>
:root{
  --blue:#2563ae;
  --blue-light:#2e8bcf;
  --blue-deep:#1f4f9a;
  --green:#8dc63f;
  --green-band:#8fcd3a;
  --yellow:#ffc214;
  --ink:#1d1d1f;
  --text:#3a3a3a;
  --navy:#0d1a2b;
  --footer:#ededef;
  --white:#fff;
}
*{box-sizing:border-box;margin:0;padding:0}
html,body{width:1200px;height:3850px;overflow:hidden;background:var(--white)}
body{position:relative;font-family:"Nunito Sans",sans-serif;color:var(--text)}
a{text-decoration:none}
.abs{position:absolute}
h1,h2,h3,.nav,.btn{font-family:"Poppins",sans-serif}
.btn{position:absolute;display:flex;align-items:center;justify-content:center;background:var(--green);color:var(--ink);font-size:15px;border-radius:2px}

/* header */
.site-header{top:0;left:0;width:1200px;height:102px;background:var(--white)}
.brand{left:143px;top:15px;display:flex;align-items:center;gap:14px}
.brand-mark{width:72px;height:72px;border-radius:50%;background:var(--blue)}
.brand-name{font-family:"Poppins",sans-serif;font-weight:600;font-size:40px;letter-spacing:4px;color:var(--blue)}
.login{left:959px;top:16px;width:96px;height:30px;font-size:15px;color:var(--white);gap:6px}
.nav{top:64px;left:520px;font-size:17px;color:var(--ink)}
.nav a{color:inherit;position:absolute;white-space:nowrap}
.nav .active{color:var(--blue)}

/* hero */
.hero{top:102px;left:0;width:1200px;height:640px}
.hero-title{top:266px;left:0;width:1200px;text-align:center;font-family:"Poppins",sans-serif;font-weight:600;font-size:48px;color:var(--yellow);letter-spacing:-.5px}

/* welcome */
.welcome-title{left:143px;top:872px;font-size:44px;font-weight:500;color:var(--blue)}
.welcome-text{left:143px;top:931px;width:430px;font-size:15px;line-height:32px;color:var(--text)}

/* services */
.services-panel{left:600px;top:1349px;width:600px;height:478px;background:linear-gradient(180deg,var(--blue-light),var(--blue-deep))}
.services-title{left:629px;top:1430px;font-size:44px;font-weight:500;color:var(--white)}
.services-text{left:629px;top:1487px;width:440px;font-size:15px;line-height:32px;color:var(--white)}

/* features */
.section-title{width:1200px;left:0;text-align:center;font-size:44px;font-weight:500}
.feature{position:absolute;width:480px;height:120px}
.feature svg{position:absolute;left:0;top:0}
.feature h3{position:absolute;left:130px;top:8px;font-size:23px;font-weight:500;color:var(--blue)}
.feature p{position:absolute;left:130px;top:48px;width:320px;font-size:12px;line-height:21px;color:var(--text)}

/* industries */
.industries{left:0;top:2331px;width:1200px;height:502px;background:var(--green-band)}
.industry-photo{position:absolute;top:2462px;height:191px}
.industry-label{position:absolute;top:2660px;font-family:"Poppins",sans-serif;font-size:25px;color:var(--ink);text-align:center}

/* blog */
.blog-title{left:397px;top:2910px;font-size:44px;font-weight:500;color:var(--blue)}
.blog-headline{left:400px;top:2984px;width:660px;font-family:"Poppins",sans-serif;font-size:25px;line-height:40px;color:var(--blue-light)}
.blog-date{left:400px;top:3080px;font-family:"Poppins",sans-serif;font-size:20px;color:var(--ink)}
.blog-text{left:400px;top:3120px;width:660px;font-size:15px;line-height:32px}

/* app band */
.app-band{left:0;top:3433px;width:1200px;height:321px;background:radial-gradient(ellipse at 30% 90%,#1d3b52 0%,var(--navy) 60%)}
.app-text{left:0;top:3515px;width:1200px;text-align:center;font-family:"Poppins",sans-serif;font-size:24px;line-height:39px;color:var(--yellow)}
.store{position:absolute;top:3611px;width:154px;height:48px;display:flex;align-items:center;gap:10px;padding-left:14px;font-size:10px;line-height:13px;border-radius:2px}
.store b{display:block;font-size:12px;font-weight:700}
.store-dot{width:22px;height:22px;border-radius:50%;flex:none}

/* footer */
.site-footer{left:0;top:3754px;width:1200px;height:96px;background:var(--footer)}
.footer-links{left:143px;top:21px;font-size:12px;color:var(--ink)}
.copyright{left:143px;top:54px;font-size:12px;color:var(--ink)}
.social{top:38px;font-size:13px;font-weight:700;color:var(--ink)}
</style>
</head>
<body>

<header class="site-header abs">
  <div class="brand abs"><span class="brand-mark"></span><span class="brand-name">VELUMAR</span></div>
  <a class="btn login" href="#">
    <svg width="14" height="14" viewBox="0 0 14 14"><path d="M1 6h7V3l4 4-4 4V8H1z" fill="#fff"/></svg>LOG IN
  </a>
  <nav class="nav abs">
    <a class="active" style="left:0">Home</a>
    <a style="left:87px">Features</a>
    <a style="left:196px">Pricing</a>
    <a style="left:289px">Services</a>
    <a style="left:395px">Blog</a>
    <a style="left:469px">Contact</a>
  </nav>
</header>

<section class="hero abs">
  <svg class="abs" width="1200" height="640" viewBox="0 0 1200 640" role="img" aria-label="Software developer working at a computer at night">
    <defs>
      <linearGradient id="heroShade" x1="0" y1="0" x2="1" y2="1">
        <stop offset="0" stop-color="#2a2f5e"/>
        <stop offset=".55" stop-color="#3b3566"/>
        <stop offset="1" stop-color="#1d2540"/>
      </linearGradient>
    </defs>
    <rect width="1200" height="640" fill="url(#heroShade)"/>
    <path d="M0 515 L600 625 L1200 515 L1200 535 L600 638 L0 535Z" fill="var(--blue-deep)"/>
    <path d="M0 535 L600 638 L1200 535 L1200 640 L0 640Z" fill="#fff"/>
    <circle cx="600" cy="226" r="28" fill="#fff"/>
    <path d="M592 212 L612 226 L592 240Z" fill="#222"/>
  </svg>
  <h1 class="hero-title abs">ETIAM VEL MASSA ELEMENTUM</h1>
</section>

<h2 class="welcome-title abs">Welcome to Velumar</h2>
<p class="welcome-text abs">Velumar Software is a mobile-first, Field Service Management &amp; CRM Software for Contractors and Home Improvement Professionals. Our software helps commercial and residential HVAC, plumbing, electrical, and other field service businesses. to send Estimates, Invoices, collect payments, manage clients and jobs from their mobile devices.</p>
<a class="btn" href="#" style="left:143px;top:1135px;width:112px;height:42px">READ MORE</a>
<svg class="abs" style="left:605px;top:819px" width="450" height="424" viewBox="0 0 450 424" role="img" aria-label="Brand emblem beside a phone showing the contractor app menu">
  <defs>
    <linearGradient id="welcomeFill" x1="0" y1="0" x2="1" y2="1">
      <stop offset="0" stop-color="#e8edf5"/>
      <stop offset="1" stop-color="#d5deec"/>
    </linearGradient>
  </defs>
  <rect width="450" height="424" rx="8" fill="url(#welcomeFill)"/>
</svg>

<svg class="abs" style="left:0;top:1325px" width="600" height="478" role="img" aria-label="Hands sketching mobile app screens with design icons on a desk">
  <rect width="600" height="478" fill="#dcdfe6"/>
</svg>
<div class="services-panel abs"></div>
<h2 class="services-title abs">Services</h2>
<p class="services-text abs">Vivamus lacus justo, ultrices nec erat in, euismod iaculis mauris. Vivamus eleifend vitae nulla vel malesuada. In ac malesuada lacus, et consectetur ante. Fusce vitae lectus sit amet mi pulvinar maximus. Aenean placerat, nibh vel accumsan aliquet, magna nibh accumsan nibh, ac tempus nunc ipsum ac tellus. Cras augue magna, placerat eget nulla.</p>
<a class="btn" href="#" style="left:629px;top:1693px;width:113px;height:42px">READ MORE</a>

<h2 class="section-title abs" style="top:1895px;color:var(--blue)">Features</h2>
<div class="feature" style="left:143px;top:1969px">
  <svg width="122" height="122" viewBox="0 0 122 122"><circle cx="61" cy="61" r="59" fill="none" stroke="var(--blue)" stroke-width="2"/><rect x="40" y="30" width="32" height="56" rx="4" fill="none" stroke="var(--blue)" stroke-width="2"/><circle cx="76" cy="66" r="11" fill="none" stroke="var(--blue)" stroke-width="2"/><path d="M47 44h18M47 52h14M47 60h10" stroke="var(--blue)" stroke-width="2"/></svg>
  <h3>Nulla facilisi</h3>
  <p>Etiam vel massa elementum, bibendum tellus venenatis, feugiat massa. Curabitur venenatis lacinia ornare.</p>
</div>
<div class="feature" style="left:626px;top:1969px">
  <svg width="122" height="122" viewBox="0 0 122 122"><circle cx="61" cy="61" r="59" fill="none" stroke="var(--blue)" stroke-width="2"/><rect x="52" y="30" width="18" height="12" fill="none" stroke="var(--blue)" stroke-width="2"/><rect x="40" y="52" width="42" height="12" fill="none" stroke="var(--blue)" stroke-width="2"/><path d="M61 42v10M46 64v10M61 64v10M76 64v10" stroke="var(--blue)" stroke-width="2"/><circle cx="46" cy="80" r="6" fill="none" stroke="var(--blue)" stroke-width="2"/><circle cx="61" cy="80" r="6" fill="none" stroke="var(--blue)" stroke-width="2"/><circle cx="76" cy="80" r="6" fill="none" stroke="var(--blue)" stroke-width="2"/></svg>
  <h3>Aliquam erat</h3>
  <p>Etiam vel massa elementum, bibendum tellus venenatis, feugiat massa. Curabitur venenatis lacinia ornare.</p>
</div>
<div class="feature" style="left:143px;top:2129px">
  <svg width="122" height="122" viewBox="0 0 122 122"><circle cx="61" cy="61" r="59" fill="none" stroke="var(--blue)" stroke-width="2"/><circle cx="48" cy="50" r="7" fill="none" stroke="var(--blue)" stroke-width="2"/><circle cx="74" cy="50" r="7" fill="none" stroke="var(--blue)" stroke-width="2"/><path d="M36 86V68q0-8 12-8t12 8v18M62 86V68q0-8 12-8t12 8v18" fill="none" stroke="var(--blue)" stroke-width="2"/><rect x="40" y="28" width="20" height="10" fill="none" stroke="var(--blue)" stroke-width="2"/></svg>
  <h3>Vivamus lacus</h3>
  <p>Etiam vel massa elementum, bibendum tellus venenatis, feugiat massa. Curabitur venenatis lacinia ornare.</p>
</div>
<div class="feature" style="left:626px;top:2129px">
  <svg width="122" height="122" viewBox="0 0 122 122"><circle cx="61" cy="61" r="59" fill="none" stroke="var(--blue)" stroke-width="2"/><path d="M38 84 L78 44 M44 90 L84 50" stroke="var(--blue)" stroke-width="2"/><circle cx="84" cy="40" r="9" fill="none" stroke="var(--blue)" stroke-width="2"/><path d="M40 38 L84 84" stroke="var(--blue)" stroke-width="4"/><circle cx="40" cy="84" r="6" fill="none" stroke="var(--blue)" stroke-width="2"/></svg>
  <h3>Cras augue</h3>
  <p>Etiam vel massa elementum, bibendum tellus venenatis, feugiat massa. Curabitur venenatis lacinia ornare.</p>
</div>

<div class="industries abs" role="img" aria-label="Green band over a faint workspace with laptop"></div>
<h2 class="section-title abs" style="top:2393px;color:var(--ink)">Industries</h2>
<svg class="industry-photo" style="left:143px" width="290" height="191" role="img" aria-label="Contractor in hard hat at a house under construction"><rect width="290" height="191" fill="#b9a58c"/></svg>
<svg class="industry-photo" style="left:456px" width="288" height="191" role="img" aria-label="Painter working on a house facade"><rect width="288" height="191" fill="#a8a49c"/></svg>
<svg class="industry-photo" style="left:766px" width="289" height="191" role="img" aria-label="Plumber adjusting a wall-mounted boiler"><rect width="289" height="191" fill="#b7c2cc"/></svg>
<div class="industry-label" style="left:143px;width:290px">Contractors</div>
<div class="industry-label" style="left:456px;width:288px">Painters</div>
<div class="industry-label" style="left:766px;width:289px">Plumbers</div>
<a class="btn" href="#" style="left:544px;top:2715px;width:112px;height:41px;background:#1e2124;color:#fff">VIEW ALL</a>

<svg class="abs" style="left:145px;top:2921px" width="206" height="423" viewBox="0 0 206 423" role="img" aria-label="Phone showing the invoice list screen of the app">
  <rect width="206" height="423" rx="24" fill="#e4e7ec"/>
</svg>
<h2 class="blog-title abs">Blog</h2>
<p class="blog-headline abs">Maecenas consequat justo enim, ac mattis massa imperdiet quis elementum in magna.</p>
<p class="blog-date abs">6 JANUARY, 2021</p>
<p class="blog-text abs">Maecenas vel tortor accumsan quam varius imperdiet vel eget elit. Aenean facilisis tincidunt lectus, id dictum nisi luctus eget. Vivamus efficitur ex condimentum, malesuada eros eget, feugiat nibh. Sed tellus ex, imperdiet eget gravida sit amet, volutpat eget turpis. In nec ultricies est. Etiam mattis augue vehicula odio posuere, sit amet tempus lectus luctus. Nulla facilisi. Etiam vel massa elementum, bibendum tellus venenatis, feugiat massa.</p>
<a class="btn" href="#" style="left:400px;top:3302px;width:113px;height:42px">READ MORE</a>

<div class="app-band abs" role="img" aria-label="Dark network background with glowing data points"></div>
<p class="app-text abs">Phasellus nisl est, condimentum vitae faucibus<br>sollicitudin vel metus. Nunc sit amet consequat risus</p>
<a class="store" href="#" style="left:438px;background:#fff;color:#222"><span class="store-dot" style="background:#2f9e5a"></span><span>Download it from<b>PINDLE SHELF</b></span></a>
<a class="store" href="#" style="left:607px;background:#14171c;color:#fff"><span class="store-dot" style="background:#fff"></span><span>Download it from<b>APDEX SHELF</b></span></a>

<footer class="site-footer abs">
  <p class="footer-links abs">Home &nbsp;&nbsp;|&nbsp;&nbsp; Features &nbsp;&nbsp;|&nbsp;&nbsp; Pricing &nbsp;&nbsp;|&nbsp;&nbsp; Services &nbsp;&nbsp;|&nbsp;&nbsp; Blog &nbsp;&nbsp;|&nbsp;&nbsp; Contact</p>
  <p class="copyright abs">Copyright © 2021 &nbsp;Velumar Software. &nbsp;All rights reserved.</p>
  <span class="social abs" style="left:984px">Fliq</span>
  <span class="social abs" style="left:1022px">Chirpa</span>
</footer>

</body>
</html>
```